Popular Golf Club needs attractive brochure

We need a brochure that will attract golfers to come to the Kestrel River area and the Brindlewood Golf Club for their golfing holiday. It also needs to address the availability of a function area and corporate functions in the clubhouse and corporate golf days on the course as well.
It will highlight our direct phone contact numbers and website as well.
We are a 36 Hole Championship Golf Course on the Kestrel River border of NSW and Victoria. 3 hours easy freeway drive from Melbourne. Over 300 sunny days every year. Fabulous golf weather all year round. Raincheck guarantee (if it rains we will give you free golf on you next visit).
The area is a golf and watersport playground. Sandy beaches, the mighty Kesterl River, home of the giant Kestrel Perch, fishing, camping, boating and golf all on your doorstep.
We can arrange Golf packages for individuals and groups including 3 and 4 star accommodation available all year round.

Target Market(s)

Golfers looking for holidays

Industry/Entity Type

Accommodation

Requirements
Must have
• Branding bar and logo. Colours signifying sun, grass and river.
Nice to have
• Smiling happy golfers, particularly more senior age group. Map of location and proximity to Melbourne. Photos of the course. some attached, many more available.

```html
<!DOCTYPE html>
<html lang="en">
<head>
<meta charset="utf-8">
<title>Brindlewood Golf Club – Brochure</title>
<link rel="stylesheet" href="https://fonts.googleapis.com/css2?family=Open+Sans:wght@400;600;700&display=swap">
<style>
  :root {
    --grass: #8cc43f;
    --river: #4fb5c9;
    --sun: #f5c518;
    --ink: #555555;
    --rule: #c9c9c9;
    --paper: #ffffff;
    --backdrop: #e9e6e1;
  }
  * { margin: 0; padding: 0; box-sizing: border-box; }
  html, body { width: 1200px; height: 969px; overflow: hidden; background: var(--backdrop); }
  body { font-family: "Open Sans", Arial, sans-serif; color: var(--ink); }

  .brochure {
    position: absolute; left: 40px; top: 53px;
    width: 1120px; height: 863px;
    background: var(--paper);
    overflow: hidden;
    box-shadow: 0 4px 14px rgba(0,0,0,0.18);
  }
  .swooshes { position: absolute; left: 0; top: 0; width: 1120px; height: 863px; }
  .fold { position: absolute; top: 0; width: 1px; height: 760px; background: var(--rule); }
  .photo { position: absolute; }

  /* left panel */
  .tag-happy {
    position: absolute; left: 50px; top: 43px; width: 280px; height: 32px;
    background: var(--grass); border-radius: 0 8px 8px 0;
    color: #fff; font-weight: 700; font-size: 19px; line-height: 32px; padding-left: 24px;
  }
  .map-area {
    position: absolute; left: 0; top: 386px; width: 367px; height: 300px;
    background: radial-gradient(ellipse at 45% 45%, #d6dad2 0%, #e4e7e1 55%, rgba(255,255,255,0) 80%);
  }

  /* middle panel */
  .shop-photo {
    left: 430px; top: 120px; width: 259px; height: 196px;
    border: 4px solid #b9b9b9;
    background: linear-gradient(180deg, #c9d3d8 0%, #a8b9a3 40%, #5f8f3c 62%, #4b7a2e 100%);
  }
  .shop-caption {
    position: absolute; left: 0; right: 0; bottom: 6px; text-align: center;
    color: var(--river); font-weight: 700; font-size: 15px;
  }
  .frame-line { position: absolute; width: 1px; height: 229px; top: 95px; background: #b9d98a; }

  .brand {
    position: absolute; display: flex; align-items: center; gap: 14px;
    font-weight: 400; color: #5a5a5a; text-transform: uppercase; white-space: nowrap;
  }
  .brand .mark { border-radius: 50%; background: var(--sun); flex: none; }
  .brand .name { line-height: 1.2; }
  .brand-mid { left: 441px; top: 378px; font-size: 17px; letter-spacing: 3px; }
  .brand-mid .mark { width: 46px; height: 46px; }
  .brand-cover { left: 768px; top: 140px; font-size: 24px; letter-spacing: 4px; }
  .brand-cover .mark { width: 74px; height: 74px; }

  .contact { position: absolute; left: 373px; width: 373px; text-align: center; }
  .contact-title { top: 458px; color: var(--sun); font-weight: 700; font-size: 26px; line-height: 36px; }
  .contact-address { top: 522px; font-size: 13px; line-height: 20px; }
  .contact-lines { top: 575px; }
  .label-sun { color: var(--sun); font-weight: 700; }
  .label-river { color: var(--river); font-weight: 700; }
  .phone-main { font-size: 18px; line-height: 24px; }
  .phone-small { font-size: 12px; line-height: 18px; }
  .email { font-size: 13px; line-height: 20px; margin-top: 18px; }
  .email .label-river { font-size: 12px; }
  .website { font-size: 19px; line-height: 26px; color: var(--river); }

  /* cover panel */
  .headline {
    position: absolute; left: 746px; width: 374px; top: 310px; text-align: center;
    font-weight: 600; line-height: 34px;
  }
  .headline .l1 { display: block; color: var(--grass); font-size: 30px; }
  .headline .l2 { display: block; color: var(--sun); font-size: 28px; }
  .headline .l3 { display: block; color: var(--river); font-size: 36px; line-height: 42px; }
  .course-photo {
    left: 747px; top: 520px; width: 373px; height: 240px;
    background: linear-gradient(180deg, #dfe9ef 0%, #7e9f63 28%, #76ad4a 55%, #3f6f2a 100%);
  }

  .footer-contact {
    position: absolute; left: 746px; width: 374px; top: 796px; text-align: center; color: #fff;
  }
  .footer-contact .phone { font-size: 19px; line-height: 28px; font-weight: 700; }
  .footer-contact .phone span { font-weight: 400; }
  .footer-contact .web { font-size: 19px; line-height: 30px; }
</style>
</head>
<body>
  <main class="brochure">
    <!-- inner left panel -->
    <div class="tag-happy">You Can Be Happy!</div>
    <div class="photo" role="img" aria-label="Trophies on display in the clubhouse" style="left:52px;top:111px;width:130px;height:100px;background:linear-gradient(135deg,#3b3128,#9a8e84 50%,#5a4b3e);"></div>
    <div class="photo" role="img" aria-label="Group of smiling golfers on the course" style="left:190px;top:103px;width:162px;height:108px;background:linear-gradient(180deg,#9fb39a 0%,#4d6f37 55%,#3a5a2a 100%);"></div>
    <div class="photo" role="img" aria-label="Guests at a corporate function in the clubhouse" style="left:21px;top:218px;width:161px;height:108px;background:linear-gradient(160deg,#6b3a22,#b07a4b 50%,#4a2a1a);"></div>
    <div class="photo" role="img" aria-label="Club courtesy bus" style="left:190px;top:218px;width:137px;height:103px;background:linear-gradient(180deg,#c9ccc8 0%,#e7ece2 45%,#7ea552 80%,#8a8a86 100%);"></div>
    <div class="map-area" role="img" aria-label="Street map showing the golf club location beside the river"></div>

    <!-- inner middle panel -->
    <div class="photo shop-photo" role="img" aria-label="Putting green in front of the club shop">
      <span class="shop-caption">Brindlewood Golf club shop</span>
    </div>
    <span class="frame-line" style="left:708px"></span>
    <span class="frame-line" style="left:715px"></span>

    <div class="brand brand-mid"><span class="mark"></span><span class="name">Brindlewood<br>Golf Club</span></div>

    <h2 class="contact contact-title">Contact us</h2>
    <p class="contact contact-address">Brindlewood Golf Club<br>Heron Rd, Brindlewood N.S.W. 2799</p>
    <div class="contact contact-lines">
      <p class="phone-main"><span class="label-sun">Phone :</span> 03 5550 0142</p>
      <p class="phone-small"><span class="label-sun">Fax :</span> 03 5550 0143</p>
      <p class="phone-small"><span class="label-sun">FREE CALL :</span> 1800 555 271</p>
      <p class="email"><span class="label-river">E-mail :</span> admin@brindlewoodgolf.com.au</p>
      <p class="website"><span class="label-river">Website :</span> www.brindlewoodgolf.com.au</p>
    </div>

    <!-- cover panel -->
    <div class="brand brand-cover"><span class="mark"></span><span class="name">Brindlewood<br>Golf Club</span></div>
    <h1 class="headline">
      <span class="l1">A great golf</span>
      <span class="l2">course is</span>
      <span class="l3">just the beginning</span>
    </h1>
    <div class="photo course-photo" role="img" aria-label="Fairway and green lined with trees"></div>

    <span class="fold" style="left:373px"></span>
    <span class="fold" style="left:746px"></span>

    <svg class="swooshes" viewBox="0 0 1120 863" aria-hidden="true">
      <!-- top right ribbon -->
      <path d="M700 0 C820 20 960 30 1120 0 L1120 10 C960 52 820 40 720 0 Z" fill="var(--river)"/>
      <path d="M720 8 C850 50 980 60 1120 22 L1120 30 C980 72 850 62 740 14 Z" fill="var(--grass)"/>
      <path d="M745 20 C870 66 990 74 1120 42 L1120 48 C990 84 870 76 760 26 Z" fill="var(--sun)"/>
      <!-- bottom: white sweep under the cover photo -->
      <path d="M600 780 C800 770 980 745 1120 705 L1120 863 L600 863 Z" fill="var(--paper)"/>
      <!-- left blue sweep -->
      <path d="M0 696 C160 712 330 740 480 772 L470 780 C320 752 160 724 0 708 Z" fill="var(--river)"/>
      <!-- yellow ribbon -->
      <path d="M0 774 C300 770 620 762 860 748 C960 742 1050 728 1120 708 L1120 720 C1050 740 960 754 860 760 C620 774 300 782 0 786 Z" fill="var(--sun)"/>
      <!-- blue ribbon -->
      <path d="M300 788 C560 782 820 772 1000 752 C1050 746 1090 738 1120 730 L1120 744 C1090 752 1050 760 1000 766 C820 786 560 794 300 796 Z" fill="var(--river)"/>
      <!-- green band -->
      <path d="M0 790 C360 790 720 786 940 770 C1020 764 1080 752 1120 744 L1120 863 L0 863 Z" fill="var(--grass)"/>
    </svg>
    <div class="footer-contact">
      <p class="phone">Phone : <span>03 5550 0142</span></p>
      <p class="web">www.brindlewoodgolf.com.au</p>
    </div>
  </main>
</body>
</html>
```